Thornbury Building Company - Card Design

I am looking to use the logo designs that you already did for me to develop a business card. I would like the card to have a black background and be double sided. I want white and green logo and text. I have attached an inspiration photo of a look that I like. I would like to use the Vertical Logo attached to take up the full front side of the card. On the back where I have my name and information, I would like to have the horizontal logo or maybe even just the image of the 'A' and trees without the text. I am open, but I am looking for something clean and simple and I want the green to really pop! Additional files can be found under Design #: 58302946

Target Market(s)

Homeowners

Industry/Entity Type

Construction

Contact Information for Business Card

Name: Marcus Thornbury, Title: Project Manager, Phone: 555.274.8136, Email: thornburybuildingcompany@mailvesta.com, address: 487 Larkspur Ln, Brookvale, OR 95033, Lic# 2468317

Colors
00AB8E
00BBA5
67D7C9
C6EFE9
E9F9F6

Requirements
Nice to have
• I would like to see the logos that I have already got from ArtLoomHub, though I am open to new ones

```html
<!DOCTYPE html>
<html lang="en">
<head>
<meta charset="utf-8">
<title>Thornbury Building Company – Business Card</title>
<link rel="stylesheet" href="https://fonts.googleapis.com/css2?family=Open+Sans:wght@400;600;700&display=swap">
<style>
  :root {
    --backdrop: #4a4a4a;
    --card-black: #141414;
    --card-light: #e3e2e2;
    --brand-green: #3cb54a;
    --text-white: #ffffff;
    --text-dark: #1e1e1e;
  }
  * { box-sizing: border-box; margin: 0; padding: 0; }
  html, body { width: 1200px; height: 801px; overflow: hidden; }
  body {
    background: var(--backdrop);
    font-family: "Open Sans", Arial, sans-serif;
    position: relative;
  }
  .card {
    position: absolute;
    top: 246px;
    width: 540px;
    height: 309px;
    background: var(--card-black);
    border-bottom: 3px solid var(--brand-green);
    border-right: 3px solid var(--brand-green);
    overflow: hidden;
  }
  .card--info { left: 40px; }
  .card--front { left: 620px; }

  .card__waves { position: absolute; inset: 0; width: 100%; height: 100%; }

  .brand-name {
    position: absolute;
    display: flex;
    align-items: center;
    gap: 8px;
    color: var(--text-white);
    font-weight: 700;
    line-height: 1.1;
    text-transform: uppercase;
    letter-spacing: 0.04em;
  }
  .brand-name__dot {
    flex: none;
    border-radius: 50%;
    background: var(--brand-green);
  }
  .brand-name--small { left: 26px; top: 58px; font-size: 10px; width: 140px; }
  .brand-name--small .brand-name__dot { width: 12px; height: 12px; }
  .brand-name--main { left: 200px; top: 46px; font-size: 22px; width: 260px; }
  .brand-name--main .brand-name__dot { width: 22px; height: 22px; }
  .brand-name--hero {
    left: 50%; top: 50%;
    transform: translate(-50%, -50%);
    font-size: 34px; width: 440px;
    justify-content: center;
  }
  .brand-name--hero .brand-name__dot { width: 34px; height: 34px; }

  .office-address {
    position: absolute;
    left: 372px; top: 136px;
    color: var(--text-white);
    font-size: 13px;
    line-height: 1.35;
    font-style: normal;
  }
  .licence {
    position: absolute;
    right: 22px; bottom: 16px;
    color: var(--text-dark);
    font-size: 13px;
  }
  .contact {
    position: absolute;
    left: 70px; top: 194px;
    color: var(--text-dark);
  }
  .contact__name { color: var(--brand-green); font-size: 21px; font-weight: 700; line-height: 1.2; }
  .contact__title { font-size: 14px; margin-bottom: 6px; }
  .contact__line { display: flex; align-items: center; gap: 7px; font-size: 13px; line-height: 1.55; }
  .contact__icon { width: 12px; height: 12px; flex: none; }
</style>
</head>
<body>

<section class="card card--info" aria-label="Card back with contact details">
  <svg class="card__waves" viewBox="0 0 540 309" preserveAspectRatio="none" aria-hidden="true">
    <path d="M0,140 C120,164 330,190 450,206 C495,212 522,216 540,222 L540,232 C525,225 500,221 450,215 C330,200 120,175 0,150 Z" fill="var(--brand-green)"/>
    <path d="M0,150 C120,175 330,200 450,215 C500,221 525,225 540,232 L540,309 L0,309 Z" fill="var(--card-light)"/>
  </svg>

  <div class="brand-name brand-name--small"><span class="brand-name__dot"></span><span>Thornbury Building Company</span></div>
  <div class="brand-name brand-name--main"><span class="brand-name__dot"></span><span>Thornbury Building Company</span></div>

  <address class="office-address">487 Larkspur Ln,<br>Brookvale, OR 95033</address>

  <div class="contact">
    <p class="contact__name">Marcus Thornbury</p>
    <p class="contact__title">Project Manager</p>
    <p class="contact__line">
      <svg class="contact__icon" viewBox="0 0 24 24" aria-hidden="true"><path fill="var(--brand-green)" d="M6.6 10.8a15.1 15.1 0 0 0 6.6 6.6l2.2-2.2a1 1 0 0 1 1-.25 11.4 11.4 0 0 0 3.6.57 1 1 0 0 1 1 1V20a1 1 0 0 1-1 1A17 17 0 0 1 3 4a1 1 0 0 1 1-1h3.5a1 1 0 0 1 1 1c0 1.25.2 2.45.57 3.57a1 1 0 0 1-.25 1z"/></svg>
      <span>555.274.8136</span>
    </p>
    <p class="contact__line">
      <svg class="contact__icon" viewBox="0 0 24 24" aria-hidden="true"><path fill="var(--brand-green)" d="M2 5h20v14H2z"/><path d="M2 5l10 8 10-8" fill="none" stroke="var(--card-light)" stroke-width="2"/></svg>
      <span>thornburybuildingcompany@mailvesta.com</span>
    </p>
  </div>

  <p class="licence">License# 2468317</p>
</section>

<section class="card card--front" aria-label="Card front">
  <div class="brand-name brand-name--hero"><span class="brand-name__dot"></span><span>Thornbury Building Company</span></div>
</section>

</body>
</html>
```